Real Estate Conference Exhibition Banner Design

We need a exhibition banner design for our company called Ledger Lantern Partners.
We are a consultancy business providing Trust Accounting, Training and Compliance services for the Real Estate Agencies around Australia. Our core focus is helping real estate agents with the Trust Accounts as an outsourced partner.

There are three banners and a case wrap all up.
The banners should use our logo colors being orange and grey.

Logo and banner templates supplied.
Upload file 5 is an example of the banner package we are purchasing.
Upload file 6,7,8 & 9 are some examples of banners we like.

our website is: ledgerlanternpartners.com.au

Target Market(s)

Real Estate Directors and Sales Agents

Industry/Entity Type

Business

Font styles to use
Sans Serif

Requirements
Must have
• Must make use of our company colours and include our logo.
Nice to have
• Would be happy to purchase stock photos

```html
<!DOCTYPE html>
<html lang="en">
<head>
<meta charset="utf-8">
<title>Ledger Lantern Partners – Exhibition Banner</title>
<link rel="stylesheet" href="https://fonts.googleapis.com/css2?family=Mulish:wght@300;400;600&display=swap">
<style>
  :root {
    --page-bg: #e8e8e8;
    --cap-grey: #7b7b7b;
    --header-light: #ecebe8;
    --body-grey: #b4b6b8;
    --body-grey-dark: #a3a5a7;
    --orange: #e27a1e;
    --band-mid: #8b8b8b;
    --band-dark: #6c6c6c;
    --band-base: #555555;
    --text-light: #f2f2f2;
    --text-grey: #6a6a6a;
    --icon-grey: #5a5a5a;
  }
  * { box-sizing: border-box; margin: 0; padding: 0; }
  html, body { width: 1200px; height: 800px; overflow: hidden; }
  body {
    background: var(--page-bg);
    font-family: "Mulish", sans-serif;
    position: relative;
  }
  .banner {
    position: absolute;
    left: 40px; top: 80px;
    width: 1120px; height: 640px;
    overflow: hidden;
    background: linear-gradient(180deg, var(--body-grey) 0%, var(--body-grey-dark) 100%);
  }
  .banner__cap {
    position: absolute; left: 0; top: 0;
    width: 100%; height: 19px;
    background: var(--cap-grey);
  }
  .banner__header {
    position: absolute; left: 0; top: 19px;
    width: 100%; height: 143px;
    background: var(--header-light);
    border-bottom: 6px solid #d2d2d2;
  }
  .brand {
    position: absolute; left: 76px; top: 30px;
    color: var(--orange);
    font-weight: 400;
    text-align: center;
  }
  .brand__dot {
    display: block;
    width: 22px; height: 22px;
    margin: 0 auto 6px;
    border-radius: 50%;
    background: var(--orange);
  }
  .brand__name {
    display: block;
    font-size: 34px;
    letter-spacing: 6px;
    line-height: 1.1;
    text-transform: uppercase;
  }
  .contact {
    position: absolute; right: 52px; top: 46px;
    text-align: right;
  }
  .contact__web {
    font-size: 29px;
    font-weight: 600;
    color: var(--text-grey);
  }
  .contact__social {
    display: flex; justify-content: flex-end; gap: 5px;
    margin-top: 12px;
  }
  .contact__social span {
    width: 28px; height: 28px;
    border-radius: 50%;
    background: var(--icon-grey);
  }
  .headline {
    position: absolute; left: 76px; top: 242px;
    font-size: 46px;
    font-weight: 300;
    line-height: 70px;
    color: var(--text-light);
    text-transform: uppercase;
    text-shadow: 0 2px 4px rgba(0,0,0,0.25);
  }
  .photo {
    position: absolute; left: 610px; top: 176px;
    width: 470px; height: 345px;
    border-radius: 40% 35% 45% 50%;
    background: radial-gradient(ellipse at 60% 45%, #e6d3c6 0%, #c9c2bd 40%, rgba(160,162,165,0) 75%);
  }
  .stripe-orange {
    position: absolute; left: 0; top: 532px;
    width: 100%; height: 22px;
    background: var(--orange);
  }
  .band-mid {
    position: absolute; left: 0; top: 554px;
    width: 100%; height: 16px;
    background: var(--band-mid);
  }
  .band-dark {
    position: absolute; left: 0; top: 570px;
    width: 100%; height: 28px;
    background: var(--band-dark);
  }
  .band-base {
    position: absolute; left: 0; top: 598px;
    width: 100%; height: 42px;
    background: var(--band-base);
  }
</style>
</head>
<body>
  <section class="banner">
    <div class="banner__cap"></div>
    <header class="banner__header">
      <div class="brand">
        <span class="brand__dot"></span>
        <span class="brand__name">Ledger Lantern<br>Partners</span>
      </div>
      <div class="contact">
        <p class="contact__web">www.ledgerlanternpartners.com.au</p>
        <div class="contact__social" aria-label="Social media links">
          <span></span><span></span><span></span><span></span>
        </div>
      </div>
    </header>
    <div class="photo" role="img" aria-label="Photo of a hand with a pencil using a calculator, cropped to the shape of Australia"></div>
    <h1 class="headline">Serving real estate<br>agencies across<br>Australia</h1>
    <div class="stripe-orange"></div>
    <div class="band-mid"></div>
    <div class="band-dark"></div>
    <div class="band-base"></div>
  </section>
</body>
</html>
```